Human Resource Consulting practice needs a business card design

We need a business card design (double sided colour) for our Human Resource (HR) consulting practice in regional New South Wales, australia. Our business name is Staff Compass. We support small and medium business across the Mid North Coast of New South Wales by providing them with outsourced HR support, services and products to help them achieve compliance with workplace legislation and across all areas of the employment lifecycle from recruitment to termination and everything in between. Our corporate colours are hot pink and black. The final design should communicate professionalism, trust, people focus.
I have attached the current (old) business card for your reference.

Target Market(s)

Business owners and high level managers

Industry/Entity Type

Business

Contact Information for Business Card

Name
Title
Phone no
Mobile no
Address
PO Box
email address
website

Colors
e34197

Requirements
Must have
• Tempate for changing business card personal details including Name, position title, mobile number, email address.
• Keep current logo and colours as per attached
• Logo must be presented in 2 colours or black only not white
Nice to have
• One side logo and graphic only other side logo and personal details
Should not have
• Should not be the same as the current version (attached) but a modern interpretation.
• Does not need a busy reverse side with our list of services as per current version. I feel this is too busy.
• No photos

```html
<!DOCTYPE html>
<html lang="en">
<head>
<meta charset="utf-8">
<title>Staff Compass – Business Card</title>
<link href="https://fonts.googleapis.com/css2?family=Michroma&display=swap" rel="stylesheet">
<style>
  :root {
    --pink: #e3199f;
    --pink-soft: #e34197;
    --black: #0b0b0b;
    --white: #ffffff;
    --paper: #f1f1f1;
    --grey: #b9b9b9;
    --stage: #d9d4cc;
  }
  * { margin: 0; padding: 0; box-sizing: border-box; }
  html, body {
    width: 1200px; height: 892px; overflow: hidden;
    background: var(--stage);
    font-family: "Michroma", sans-serif;
  }
  .canvas {
    position: relative; width: 1200px; height: 892px;
  }
  .card {
    position: absolute; top: 166px;
    width: 340px; height: 560px;
    border-radius: 18px; overflow: hidden;
    box-shadow: 0 10px 30px rgba(0,0,0,0.25);
  }
  .card--front { left: 220px; background: var(--black); }
  .card--back  { left: 640px; background: var(--paper); }

  .band { position: absolute; left: 0; width: 100%; background: var(--pink); }
  .band--top { top: 0; height: 44px; }
  .band--bottom { bottom: 0; height: 96px; }

  .brand {
    position: absolute; left: 36px; top: 96px;
    display: flex; align-items: center; gap: 10px;
    color: var(--pink); font-size: 25px; line-height: 1;
  }
  .brand__mark { width: 12px; height: 12px; background: var(--white); }

  .person { position: absolute; left: 36px; top: 210px; }
  .person__name { color: var(--pink); font-size: 24px; letter-spacing: 1px; }
  .person__title { color: var(--grey); font-size: 9px; letter-spacing: 1.5px; margin-top: 6px; }

  .contacts { position: absolute; left: 36px; top: 296px; list-style: none; }
  .contacts li {
    display: flex; align-items: center; gap: 10px;
    color: var(--white); font-size: 11px; letter-spacing: 0.8px;
    height: 22px;
  }
  .contacts .icon { width: 15px; height: 15px; flex: none; }
  .contacts .address { color: var(--grey); display: block; height: auto; padding-left: 0; margin-top: 4px; line-height: 1.6; font-size: 10.5px; }

  .back-brand {
    position: absolute; left: 170px; top: 40px;
    transform-origin: left top; transform: rotate(90deg) translateY(-110px);
    display: flex; align-items: center; gap: 14px;
    color: var(--black); font-size: 40px; white-space: nowrap;
  }
  .back-brand__mark { width: 18px; height: 18px; background: var(--pink); }
</style>
</head>
<body>
<div class="canvas">

  <section class="card card--front" aria-label="Card front">
    <div class="band band--top"></div>
    <div class="brand"><span class="brand__mark"></span><span>Staff Compass</span></div>

    <div class="person">
      <div class="person__name">Maren Lowe</div>
      <div class="person__title">PRINCIPAL CONSULTANT</div>
    </div>

    <ul class="contacts">
      <li>
        <svg class="icon" viewBox="0 0 16 16"><rect width="16" height="16" rx="2" fill="var(--pink)"/><path d="M4 4h3l1 3-1.5 1a6 6 0 0 0 2.5 2.5L10 9l3 1v3c-5 0-9-4-9-9z" fill="#fff"/></svg>
        <span>02 5550 1842</span>
      </li>
      <li>
        <svg class="icon" viewBox="0 0 16 16"><rect width="16" height="16" rx="2" fill="var(--pink)"/><rect x="5" y="3" width="6" height="10" rx="1" fill="#fff"/><rect x="6" y="4.5" width="4" height="6" fill="var(--pink)"/></svg>
        <span>0491 570 156</span>
      </li>
      <li>
        <svg class="icon" viewBox="0 0 16 16"><rect width="16" height="16" rx="2" fill="var(--pink)"/><rect x="5" y="3" width="6" height="4" fill="#fff"/><rect x="3" y="7" width="10" height="5" rx="1" fill="#fff"/><rect x="5" y="10" width="6" height="3" fill="var(--pink)"/></svg>
        <span>02 5550 1877</span>
      </li>
      <li>
        <svg class="icon" viewBox="0 0 16 16"><rect width="16" height="16" rx="2" fill="var(--pink)"/><circle cx="8" cy="8" r="4.5" fill="none" stroke="#fff" stroke-width="1.2"/><path d="M3.5 8h9M8 3.5c-2 2.5-2 6.5 0 9M8 3.5c2 2.5 2 6.5 0 9" fill="none" stroke="#fff" stroke-width="1"/></svg>
        <span>www.staffcompass.com.au</span>
      </li>
      <li>
        <svg class="icon" viewBox="0 0 16 16"><rect width="16" height="16" rx="2" fill="var(--pink)"/><rect x="3" y="4.5" width="10" height="7" fill="#fff"/><path d="M3 4.5l5 4 5-4" fill="none" stroke="var(--pink)" stroke-width="1.2"/></svg>
        <span>maren@staffcompass.com.au</span>
      </li>
      <li class="address">PO Box 218, Harbourview,<br>NSW 2400</li>
    </ul>

    <div class="band band--bottom"></div>
  </section>

  <section class="card card--back" aria-label="Card back">
    <div class="back-brand"><span class="back-brand__mark"></span><span>Staff Compass</span></div>
    <div class="band band--bottom"></div>
  </section>

</div>
</body>
</html>
```